Lurvik.no is a new website about pedagogical entrepreneurship. It's main target group is teachers. The Nordic Bureau for Digital Schooling and the National Office for Learning and Classrooms are leading the project.

The web page is meant to show examples of how different methods of entrepreneurship can be used pedagogical in a learning environment. The page will also support the user with examples of different teaching programs and other examples of best practice.

Pedagogical entrepreneurship is not about business and men in suits. It's a method for learning. The focus in the design should be on school, education and new ways of learning.

The final product should be motivating and engaging, but at the same time governmental and serious. We are not looking for something "flashy" and corporate-looking, but a moderate, task-focused and clean design that state quality.

We need designs for three pages:
1 - frontpage
2 - subpage ("Metoder og undervisningsopplegg")
3 - subpage ("Små-TOPP i Vassbygd")

The interaction design for these three pages will be uploaded as an attachment.

We would like you to find inspiration in the following websites:
- www.skapekraft.no
- www.giellu.no
- www.brightfernlab.com
- www.zyx.no
(more will be added)

Please use the attached logo, and feel free to use this as an inspiration for the rest of the design.

Target Market(s)

Teachers

Industry/Entity Type

Education

Requirements
Must have
• * Header with: Logo. Main navigation. Utility navigation. Search box.
* Footer
Should not have
• Images of men in suits.
Very strong graphical elements that stands out too much (we want it clean).

```html
<!DOCTYPE html>
<html lang="en">
<head>
<meta charset="utf-8">
<title>Lurvik.no – Pedagogical entrepreneurship</title>
<link rel="stylesheet" href="https://fonts.googleapis.com/css2?family=PT+Sans:ital,wght@0,400;0,700;1,400&family=Arimo:wght@400;700&family=Lora:ital,wght@1,400;1,700&display=swap">
<style>
:root{
  --navy:#0b3a6e;
  --navy-deep:#062a55;
  --blue:#1a6bb0;
  --blue-bright:#2f8fe0;
  --sky:#a8d4f6;
  --sky-light:#cfe7fb;
  --grey-band:#e6e6e6;
  --panel-grey:#efefef;
  --orange:#f28a1c;
  --green:#5f9a1f;
  --rust:#b9501b;
  --yellow:#ffd41c;
  --text:#222;
  --link:#1a6bb0;
  --white:#fff;
}
*{box-sizing:border-box;margin:0;padding:0}
html,body{width:867px;height:1200px;overflow:hidden}
body{position:relative;background:var(--white);font-family:"Arimo",Arial,sans-serif;color:var(--text)}
.abs{position:absolute}
.top-band{left:0;top:0;width:867px;height:455px;background:var(--grey-band)}
.header-shape{left:0;top:0;width:867px;height:440px}
.search{left:628px;top:11px;width:136px;height:19px;border-radius:10px;background:#f7f7f7;border:1px solid #c9c9c9;font:italic 9px "Arimo",sans-serif;color:#999;padding:4px 10px;overflow:hidden}
.search-btn{position:absolute;right:0;top:0;width:20px;height:17px;background:#6db33f;border-radius:0 9px 9px 0}
.search-btn svg{position:absolute;left:5px;top:3px}
.brand{left:112px;top:30px;display:flex;align-items:center;gap:10px}
.brand-mark{width:48px;height:48px;border-radius:50%;background:#7fbfee}
.brand-name{font:700 40px/1 "PT Sans",sans-serif;color:#5db4f0}
.tagline{left:181px;top:71px;font:9px "PT Sans",sans-serif;color:#dbeeff}
.main-nav{left:421px;top:61px;display:flex;gap:21px;font:700 12px "PT Sans",sans-serif;color:#8fd0ff;text-transform:uppercase}
.intro{left:95px;top:94px;width:677px;height:200px;background:linear-gradient(#cde6fa,#9fcdf3);border-radius:5px}
.intro p{position:absolute;left:25px;top:12px;width:610px;font:italic 16px/1.22 "Lora",serif;color:#1e3a5c}
.intro b{color:#123}
.learn-more{right:24px;top:54px;font:italic 16px "Lora",serif;color:#111}
.features{left:108px;top:175px;width:651px;height:303px;border-radius:4px;background:radial-gradient(ellipse at 50% 30%,#4ba3e6,#1c5fa6 80%);border:2px solid #cfe7fb}
.card{top:190px;width:191px;height:272px;border-radius:8px;border:2px solid #fff;overflow:hidden;text-align:center;color:#fff}
.card-kicker{margin-top:10px;font:12px "PT Sans",sans-serif}
.card-title{font:20px/1.1 "PT Sans",sans-serif}
.card-orange{left:123px;background:linear-gradient(#f6a02f,var(--orange) 40%,#5aa6e6 60%)}
.card-green{left:338px;background:linear-gradient(#6fab2a,var(--green) 40%,#5aa6e6 60%)}
.card-rust{left:553px;background:linear-gradient(#c65b22,var(--rust) 40%,#5aa6e6 60%)}
.card-art{position:absolute;left:2px;top:82px;width:183px;height:183px;border-radius:50%;border:5px solid #e9eef3;background:radial-gradient(#ffffff,#e4e8ec)}
.started-left{left:95px;top:513px;width:229px;height:278px;background:linear-gradient(#1b6cb8,#0f4f95)}
.started-left h3{margin-top:12px;text-align:center;font:400 17px/1.05 "PT Sans",sans-serif;color:#fff}
.gauge{position:absolute;left:40px;top:65px;width:150px;height:150px;border-radius:50%;background:radial-gradient(#3a3f45 0,#15181c 62%,#cfd6dd 64%,#8e99a4 72%,#e5ebf0 76%)}
.try-btn{position:absolute;left:27px;top:228px;width:175px;height:35px;border-radius:4px;background:linear-gradient(#ffe24a,#f7b80f);font:700 14px/35px "PT Sans",sans-serif;color:#1c3e78;text-align:center;border:1px solid #e5a000}
.started-right{left:324px;top:513px;width:448px;height:278px;background:var(--panel-grey);border-radius:0 4px 4px 0}
.started-right h2{position:absolute;left:14px;top:18px;font:400 21px "PT Sans",sans-serif;color:#111}
.list-box{top:572px;height:205px;background:#fff;border:1px solid #ddd;border-radius:5px;padding:10px 13px}
.list-box h4{font:700 11px "Arimo",sans-serif;color:var(--link);padding-bottom:8px;border-bottom:1px dotted #bbb;margin-bottom:10px}
.list-box ul{list-style:none}
.list-box li{font:8.5px/17px "Arimo",sans-serif;color:#333;padding-left:14px;position:relative}
.list-box li::before{content:"";position:absolute;left:0;top:4px;width:9px;height:9px;border-radius:50%;background:#7ab7e5}
.see-more{display:block;margin-top:4px;font:8.5px "Arimo",sans-serif;color:var(--link)}
.inspiration-title{left:102px;top:806px;font:400 20px "PT Sans",sans-serif;color:var(--blue)}
.carousel{left:98px;top:842px;width:670px;height:153px;background:var(--blue-bright);border-left:4px solid var(--navy);border-right:4px solid var(--navy);border-radius:3px}
.arrow{top:914px;width:13px;height:17px;background:var(--navy)}
.photo{top:856px;width:139px;height:93px;border:3px solid #fff}
.caption{top:960px;font:9.5px/1.25 "Arimo",sans-serif;color:#fff}
.footer{left:0;top:1022px;width:867px;height:178px;background:linear-gradient(#1763a8,#0b3f7c)}
.footer-brand{left:108px;top:1068px;display:flex;align-items:center;gap:8px}
.footer-brand span{font:700 26px "PT Sans",sans-serif;color:#fff}
.footer-brand i{display:block;width:26px;height:26px;border-radius:50%;background:#5aa8e6}
.fcol{top:1041px;font:9px/15.5px "PT Sans",sans-serif;color:#cfe6fb}
.fcol h5{font:700 11px/1 "PT Sans",sans-serif;color:#fff;margin-bottom:10px}
.fcol .more{color:#ffd41c}
.footer-rule{left:100px;top:1162px;width:670px;height:1px;background:#3a78b8}
.copyright{left:103px;top:1173px;font:9px "PT Sans",sans-serif;color:#fff}
.share{left:663px;top:1172px;display:flex;gap:7px;align-items:center;font:11px "PT Sans",sans-serif;color:#fff}
.share i{display:block;width:16px;height:16px;border-radius:2px;background:#5a8fd0}
</style>
</head>
<body>
<div class="abs top-band"></div>
<svg class="abs header-shape" viewBox="0 0 867 440" aria-hidden="true">
  <defs><linearGradient id="hdr" x1="0" y1="0" x2="0" y2="1"><stop offset="0" stop-color="#1d4f8a"/><stop offset="1" stop-color="#062a55"/></linearGradient></defs>
  <polygon points="37,2 858,58 848,436 8,382" fill="url(#hdr)"/>
</svg>

<header>
  <div class="abs search">search...<span class="search-btn"><svg width="10" height="10" viewBox="0 0 10 10"><circle cx="4" cy="4" r="3" fill="none" stroke="#fff" stroke-width="1.5"/><line x1="6" y1="6" x2="9" y2="9" stroke="#fff" stroke-width="1.5"/></svg></span></div>
  <div class="abs brand"><span class="brand-mark"></span><span class="brand-name">Lurvik</span></div>
  <div class="abs tagline">Entreprenørielle metoder i undervisningen</div>
  <nav class="abs main-nav"><span>Best practice schools</span><span>Lurvikmeter</span><span>About Lurvik.no</span></nav>
</header>

<section class="abs intro">
  <p><b>Pedagogical entrepreneurship works.</b> Lorem ipsum dolor sit amet, consectetur adipisicing elit, sed do eiusmod tempor incididunt ut labore et dolore magna aliqua.</p>
  <span class="abs learn-more">Learn more ›</span>
</section>

<div class="abs features"></div>
<article class="abs card card-orange">
  <p class="card-kicker">Learn about what, why and how!</p>
  <p class="card-title">What is pedagocical entrepreneurship?</p>
  <div class="card-art" role="img" aria-label="Hand-drawn answer sheet titled Solution with options A to D"></div>
</article>
<article class="abs card card-green">
  <p class="card-kicker">Plan your lessons!</p>
  <p class="card-title">Methods and teaching plans</p>
  <div class="card-art" role="img" aria-label="Hand-drawn sketch of a light bulb and steps from think to success"></div>
</article>
<article class="abs card card-rust">
  <p class="card-kicker">Be inspired!</p>
  <p class="card-title">Good examples / best practice</p>
  <div class="card-art" role="img" aria-label="Hand-drawn checklist with one ticked box"></div>
</article>

<section class="abs started-left">
  <h3>Are you working<br>entrepreneurship-like?</h3>
  <div class="gauge" role="img" aria-label="Speedometer gauge illustration"></div>
  <div class="try-btn">Try the Lurvikmeter!</div>
</section>
<section class="abs started-right"><h2>Get started!</h2></section>
<div class="abs list-box" style="left:338px;width:203px">
  <h4>Methods</h4>
  <ul><li>Cafe-pedagogikk</li><li>Elevbedrift</li><li>Grundercamp</li><li>Story line</li><li>REAL</li><li>Grundercamp</li><li>Story line</li><li>REAL</li></ul>
  <a class="see-more">See more...</a>
</div>
<div class="abs list-box" style="left:554px;width:204px">
  <h4>Teaching plans</h4>
  <ul><li>Teaching plans title</li><li>Teaching plans title</li><li>Teaching plans title</li><li>Teaching plans title</li><li>Teaching plans title</li><li>Teaching plans title</li><li>Teaching plans title</li><li>Teaching plans title</li></ul>
  <a class="see-more">See more...</a>
</div>

<h2 class="abs inspiration-title">Inspiration</h2>
<div class="abs carousel"></div>
<span class="abs arrow" style="left:102px"></span>
<span class="abs arrow" style="left:752px"></span>
<div class="abs photo" style="left:123px;background:linear-gradient(#a86a3e,#6e4a3a)" role="img" aria-label="Photo of students working together around a table"></div>
<div class="abs photo" style="left:284px;background:linear-gradient(#c9c2b6,#7d7466)" role="img" aria-label="Photo of a seminar audience taking notes"></div>
<div class="abs photo" style="left:445px;background:linear-gradient(#6fa3c8,#c97a4a)" role="img" aria-label="Photo of a teacher in a classroom"></div>
<div class="abs photo" style="left:606px;background:linear-gradient(#e8eef4,#9aa3ad)" role="img" aria-label="Photo of a cheering group of people"></div>
<p class="abs caption" style="left:123px">Lorem ipsum dolor<br>sed do eiusmod</p>
<p class="abs caption" style="left:284px">Lorem ipsum dolor<br>sed do eiusmod</p>
<p class="abs caption" style="left:445px">Lorem ipsum dolor<br>sed do eiusmod</p>
<p class="abs caption" style="left:606px">Lorem ipsum dolor<br>sed do eiusmod</p>

<footer>
  <div class="abs footer"></div>
  <div class="abs footer-brand"><i></i><span>Lurvik</span></div>
  <div class="abs fcol" style="left:227px"><h5>Pedagogical entrepreneurship</h5>What is pedagogical entrepreneurship?<br>Science<br>Best practice schools<br>Lurvikmeter<br>About lurvik.no</div>
  <div class="abs fcol" style="left:425px"><h5>Methoda</h5>Storyline<br>REAL<br>Cafe-pedagogikk<br><span class="more">See more...</span></div>
  <div class="abs fcol" style="left:539px"><h5>Teaching plans</h5>Lorem ipsum dolor<br>sed do eiusmod<br>Lorem ipsum dolor<br>sed do eiusmod<br><span class="more">See more...</span></div>
  <div class="abs fcol" style="left:665px"><h5>Gode eksemplert</h5>Lorem ipsum dolor<br>sed do eiusmod<br>Lorem ipsum dolor<br>sed do eiusmod<br><span class="more">See more...</span></div>
  <div class="abs footer-rule"></div>
  <p class="abs copyright">© 2011 Pedagogical entrepreneurship.</p>
  <div class="abs share">Share this! <i></i><i></i></div>
</footer>
</body>
</html>
```